BRIGHTHOLD PROPERTY MANAGEMENT INC. WEBSITE

Please make the website more family-friendly.

I want a website to help me build my property management business by adding listing properties and creating an online application. Im open to any other ideas.
I want a WordPress designer to code it.

Here is my current website. www.brighthold.biz

IDEA: I like the website design https://www.pelicanclimateservices.com/

Thank you

Tom

Number of Pages Required

5+ page

```html
<!DOCTYPE html>
<html lang="en">
<head>
<meta charset="utf-8">
<title>Brighthold Property Management</title>
<link href="https://fonts.googleapis.com/css2?family=Fira+Sans:wght@400;500;600;700&family=Arimo:wght@400;700&display=swap" rel="stylesheet">
<style>
:root{
  --band:#a30d14;
  --brand:#e8141b;
  --footer:#f01010;
  --ink:#1a1a1a;
  --muted:#555;
  --grey-bar:#7b7b7b;
  --panel:#e7e7e9;
  --link:#12b5e8;
  --price:#2aa81a;
  --field:#b9b9b9;
}
*{box-sizing:border-box;margin:0;padding:0}
html,body{width:1200px;height:4162px;overflow:hidden;background:#fff}
body{font-family:"Arimo",Arial,sans-serif;color:var(--ink)}
.page{position:relative;width:1200px;height:4162px;overflow:hidden}
.abs{position:absolute}
.head-font{font-family:"Fira Sans",Arial,sans-serif}

/* header */
.brand-name{left:20px;top:44px;font-family:"Fira Sans",sans-serif;font-weight:700;font-size:22px;color:var(--band);display:flex;align-items:center;gap:8px}
.brand-name i{width:16px;height:16px;background:var(--band);display:block}
.main-nav{left:320px;top:70px;font-family:"Fira Sans",sans-serif;font-size:25px;color:#222;display:flex}
.main-nav span{margin-right:22px}
.main-nav span:nth-child(3){margin-right:48px}
.main-nav span:nth-child(4){margin-right:28px}
.main-nav span:nth-child(5){margin-right:36px}

/* hero */
.hero{left:0;top:124px;width:1200px;height:532px;background:
  radial-gradient(ellipse 340px 300px at 640px 300px,#e8481c 0%,rgba(200,50,20,.6) 45%,transparent 75%),
  linear-gradient(180deg,#0d1f3e 0%,#1f3566 35%,#5a2a2a 70%,#2a1a12 100%)}
.hero-title{right:24px;top:510px;font-family:"Fira Sans",sans-serif;font-weight:600;font-size:78px;color:#fff;text-align:right;line-height:1}
.hero-sub{right:26px;top:600px;font-family:"Fira Sans",sans-serif;font-weight:500;font-size:25px;color:#fff}

/* services */
.service{top:700px;width:200px;text-align:center;font-family:"Fira Sans",sans-serif;font-weight:600;font-size:10.5px;color:var(--brand)}
.service svg{display:block;margin:0 auto 14px}

/* about */
.about-title{left:60px;top:916px;font-family:"Fira Sans",sans-serif;font-weight:500;font-size:39px;line-height:48px}
.about-text{left:60px;top:1033px;width:670px;font-size:16.6px;line-height:20px}
.about-text p{margin-bottom:20px}
.areas{left:796px;top:1024px;width:380px;height:400px;background:var(--panel);border:3px solid #555;display:flex}
.areas ul{list-style:none;padding-top:4px;font-size:11.6px;color:#666}
.areas ul:first-child{width:152px;border-right:1px solid #999;padding-left:14px}
.areas ul:last-child{padding-left:18px}
.areas li{height:30.1px;line-height:30.1px;white-space:nowrap}
.areas li::before{content:"•";margin-right:8px;color:#777}

/* listing */
.section-h{font-family:"Fira Sans",sans-serif;font-weight:600;color:#111}
.listing-h{left:0;width:1216px;top:1562px;text-align:center;font-size:30px}
.feature{left:79px;top:1628px;width:1063px;height:391px;background:#fff;box-shadow:0 1px 6px rgba(0,0,0,.18);border-bottom:3px solid #c0393f}
.feature-photo{left:79px;top:1628px;width:452px;height:316px;background:linear-gradient(180deg,#c9dbe8 0%,#d8c4a2 60%,#8d7a5c 100%)}
.thumb{top:1957px;height:43px;background:linear-gradient(180deg,#9fb2c4,#c9a98a)}
.feature-info{left:567px;top:1638px;font-size:20.5px;line-height:24px}
.feature-info h3{font-weight:700;font-size:20.5px;margin-bottom:8px}
.feature-info .price{color:var(--price);font-weight:700;font-size:20.5px;margin-bottom:18px}
.feature-info p{margin-bottom:18px}
.card{top:2074px;height:423px;background:#fff;box-shadow:0 1px 6px rgba(0,0,0,.2)}
.card .photo{height:286px}
.card h4{font-family:"Fira Sans",sans-serif;font-weight:400;font-size:24px;margin:24px 0 0 20px}
.card p{font-family:"Fira Sans",sans-serif;font-size:12px;margin:10px 0 0 20px;word-spacing:2px}
.card p span{margin-right:14px}

/* tenant */
.tenant-bar{left:15px;top:2532px;width:1185px;height:79px;background:var(--grey-bar);color:#fff;text-align:center;font-family:"Fira Sans",sans-serif;font-weight:600;font-size:32px;line-height:79px}
.tenant-photo{left:19px;top:2636px;width:598px;height:345px;background:linear-gradient(160deg,#d7dee6 0%,#a9563e 45%,#7a3b2b 75%,#8a8f7a 100%)}
.tenant-text{left:640px;top:2638px;width:525px;font-size:11.7px;line-height:14.4px}
.tenant-text p{margin-bottom:14px}
.read-more{left:643px;top:2960px;font-weight:700;font-size:15.5px;color:var(--link)}
.policy{left:210px;top:3040px;width:800px;text-align:center;font-size:12px;line-height:15px}
.contact{left:225px;top:3121px;font-size:12px;line-height:15.5px}
.contact u{text-decoration:underline}
.lbl{font-size:12px;color:#222}
.field{height:27px;border:1px solid var(--field);border-radius:9px;font-size:11.5px;color:#999;padding:6px 10px;width:209px}
.btn{top:3432px;height:32px;width:107px;border-radius:7px;background:var(--band);color:#fff;font-weight:700;font-size:12px;text-align:center;line-height:32px}

/* mortgage */
.mortgage-h{left:440px;top:3545px;font-size:31px}
.red-h{font-family:"Fira Sans",sans-serif;font-weight:600;color:var(--band);font-size:20px}
.summary{left:84px;top:3663px;font-size:11.2px;line-height:12.8px}
.summary b{color:var(--band);display:block;margin-bottom:6px}
.summary div{display:flex}
.summary div span:first-child{width:128px}
.params-h{left:388px;top:3663px;font-size:11.2px;font-weight:700;color:var(--band)}
.small{font-size:11.2px}
.mini{height:21px;border:1px solid #888;border-radius:5px;font-size:11px;padding:3px 10px}
.calc-btn{left:388px;top:3821px;width:72px;height:23px;background:var(--brand);color:#fff;border-radius:3px;font-size:11.5px;text-align:center;line-height:23px}
.rates{left:772px;top:3674px;width:388px;height:163px;border:1px solid #777;border-radius:8px;font-size:11.5px;padding:26px 20px 0 18px;line-height:14.6px}
.rates .row{display:flex;justify-content:space-between}
.rates .gap{height:16px}
.rates .note{margin-top:16px;font-size:10.8px}

/* footer */
.footer{left:0;top:3879px;width:1200px;height:283px;background:var(--footer);color:#fff}
.foot-brand{left:78px;top:3966px;font-family:"Fira Sans",sans-serif;font-weight:700;font-size:24px;color:#fff;display:flex;align-items:center;gap:8px}
.foot-brand i{width:14px;height:14px;background:#fff;display:block}
.foot-nav{font-family:"Fira Sans",sans-serif;font-size:23px;line-height:34px;color:#fff}
.foot-nav div::before{content:"✔";font-size:18px;margin-right:6px}
.mascot{left:937px;top:3924px;width:226px;height:210px;border-radius:40px;background:linear-gradient(160deg,#f6c243 0%,#e88d3a 60%,#c9d8ee 100%)}
.legal{left:0;width:1200px;top:4104px;text-align:center;font-size:15.5px;line-height:23px;color:#fff}
</style>
</head>
<body>
<div class="page">

  <!-- Header -->
  <header>
    <div class="abs brand-name"><i></i>BRIGHTHOLD</div>
    <nav class="abs main-nav">
      <span>Listing</span><span>Owners</span><span>Prospect Tenants</span><span>About</span><span>Comunnity</span><span>Mortgage Info</span>
    </nav>
  </header>

  <!-- Hero -->
  <section>
    <div class="abs hero" role="img" aria-label="Night view of the lit-up lift bridge and downtown skyline reflected in the river"></div>
    <div class="abs hero-title">Call Today</div>
    <div class="abs hero-sub">&amp; Get 1 Month Property Management Fee Off. $120 Value!!</div>
  </section>

  <!-- Services -->
  <section>
    <div class="abs service" style="left:364px">
      <svg width="70" height="70" viewBox="0 0 70 70" aria-hidden="true">
        <g fill="#e8141b">
          <rect x="6" y="2" width="14" height="14" rx="2"/>
          <rect x="6" y="28" width="14" height="14" rx="2"/>
          <rect x="6" y="54" width="14" height="14" rx="2"/>
          <rect x="28" y="4" width="38" height="5"/><rect x="28" y="12" width="38" height="5"/>
          <rect x="28" y="30" width="38" height="5"/><rect x="28" y="38" width="38" height="5"/>
          <rect x="28" y="56" width="38" height="5"/><rect x="28" y="64" width="38" height="4"/>
        </g>
      </svg>
      FULL SERVICE MANAGEMENT
    </div>
    <div class="abs service" style="left:612px">
      <svg width="74" height="70" viewBox="0 0 74 70" aria-hidden="true">
        <path d="M37 2 L72 32 L64 32 L64 68 L10 68 L10 32 L2 32 Z" fill="#e8141b"/>
        <text x="37" y="60" text-anchor="middle" font-family="Fira Sans, sans-serif" font-weight="700" font-size="34" fill="#fff">$</text>
      </svg>
      RENT UP ONLY
    </div>
  </section>

  <!-- Band 1 -->
  <svg class="abs" style="left:0;top:832px" width="1200" height="84" aria-hidden="true">
    <path d="M0 0 H1200 V30 Q600 55 0 84 Z" fill="var(--band)"/>
  </svg>

  <!-- About -->
  <section>
    <h1 class="abs about-title">Property Management Elk Grove, Sacramento &amp;<br>Surrounding Areas</h1>
    <div class="abs about-text">
      <p>Having the right property manager means having an agent who is committed to helping you and making being a home provider hassle free. I believe clear communication, work ethic, time management, staying focused and knowledge goes a long way in my business.</p>
      <p>This commitment level has helped us build a remarkable track record of delivering results and maintaining a long lasting business partnership with our clients.</p>
      <p>Additionally whether you are an experienced investor or a first time home seller or buyer, we can help you in finding the property of your dreams. We truly feel excited and gratified when helping individuals meet their real estate needs. You can count on us to always do what's in your best interest. We pride ourselves on being honest, trustworthy, and knowledgeable in the real estate market. We know how important it is to find your dream home or receive the best offer for your property. Therefore we will make it our responsibility to help you achieve those goals.</p>
      <p>Please feel free to browse our website, you can contact us via e-mailing or better yet contact us personally by calling and setting up an appointment today.</p>
    </div>
    <div class="abs areas">
      <ul>
        <li>Sacramento</li><li>Antelope</li><li>Carmichael</li><li>Citrus Heights</li><li>El Dorado County</li><li>El Dorado Hills</li><li>Elverta</li><li>Fair Oaks</li><li>Folsom</li><li>Foothill Farms</li><li>Florin Vicinity</li><li>Land Park / Curtis Park</li><li>Galt</li>
      </ul>
      <ul>
        <li>Elk Grove / Laguna</li><li>Mather</li><li>Natomas</li><li>North Highlands</li><li>Orangevale</li><li>Rancho Cordova / Gold River</li><li>Rancho Cordova / Anatolia &amp; Vicinity</li><li>Rancho Murieta</li><li>Rio Linda</li><li>Rocklin</li><li>Rosemont / Mayhew Vicinity</li><li>Roseville</li><li>West Sacramento</li>
      </ul>
    </div>
  </section>

  <!-- Band 2 -->
  <svg class="abs" style="left:0;top:1453px" width="1200" height="90" aria-hidden="true">
    <path d="M0 50 Q600 30 1200 0 V90 H0 Z" fill="var(--band)"/>
  </svg>

  <!-- Listing -->
  <section>
    <h2 class="abs section-h listing-h">LISTING</h2>
    <div class="abs feature"></div>
    <div class="abs feature-photo" role="img" aria-label="Single-storey ADU unit with wooden steps beside a large tree, with a branded sign overlay"></div>
    <div class="abs thumb" style="left:107px;width:56px" role="img" aria-label="Gallery thumbnail"></div>
    <div class="abs thumb" style="left:186px;width:61px" role="img" aria-label="Gallery thumbnail"></div>
    <div class="abs thumb" style="left:266px;width:54px" role="img" aria-label="Gallery thumbnail"></div>
    <div class="abs thumb" style="left:342px;width:54px" role="img" aria-label="Gallery thumbnail"></div>
    <div class="abs thumb" style="left:415px;width:36px;background:#e7e7e7" role="img" aria-label="Gallery thumbnail"></div>
    <div class="abs thumb" style="left:472px;width:56px" role="img" aria-label="Gallery thumbnail"></div>
    <div class="abs feature-info">
      <h3>Fantastic opportunity 2 Bdrm x 1 Bth ADU Unit!!</h3>
      <div class="price">$2,000.00</div>
      <p>1418 Cedar Grove Ave<br>Oakland, CA 94621<br>Alameda, US</p>
      <p>Status: Available Type: Residential<br>Size: 693 Sq.Ft. Bedrooms: 2 Bathrooms: 1</p>
    </div>

    <article class="abs card" style="left:76px;width:370px">
      <div class="photo" role="img" aria-label="Modern two-storey farmhouse at dusk with lit garage doors" style="background:linear-gradient(180deg,#8f86b0 0%,#d0b8c8 45%,#4a4a4e 75%,#7b8a5a 100%)"></div>
      <h4>Luxury Farmhouses</h4>
      <p><span>Status: Available</span>Type: Residential</p>
    </article>
    <article class="abs card" style="left:475px;width:371px">
      <div class="photo" role="img" aria-label="Two-storey suburban house with a for-rent sign on the lawn" style="background:linear-gradient(180deg,#9cc3e6 0%,#ece6d8 45%,#b8232c 65%,#5f8a3a 100%)"></div>
      <h4>Big House</h4>
      <p><span>Status: Rented</span>Type: Residential</p>
    </article>
    <article class="abs card" style="left:875px;width:340px">
      <div class="photo" role="img" aria-label="Row of new tan two-storey homes on a sunny street" style="background:linear-gradient(180deg,#7fb3e8 0%,#d9c3a6 45%,#b7926e 70%,#8e9a7a 100%)"></div>
      <h4>Best House</h4>
      <p><span>Status: Available</span>Type: Residential</p>
    </article>
  </section>

  <!-- Tenant application -->
  <section>
    <div class="abs tenant-bar">Tenant Application</div>
    <div class="abs tenant-photo" role="img" aria-label="Family with an agent outside a brick house with a for-sale sign"></div>
    <div class="abs tenant-text">
      <p><b>Rental Applicants and Prospective Tenants<br>QUALIFYING FOR A RENTAL</b></p>
      <p><b>INCOME</b>: In order to rent a residential home from Brighthold Property Management Inc., applicants must be able to show that their monthly income is equal to or greater than 3 times the monthly rent. We consider all verifiable income of all applicants in the household. Self-employed persons may need to submit tax returns and / or bank statements.</p>
      <p><b>CREDIT REPORTS</b>: The credit report is one of several factors we use in choosing a tenant. Although a high credit rating is preferable, we recognize that many potentially great tenants have had credit problems in the past. If your credit history is less than perfect we will look to see how long ago your credit problems occurred and assess where you are today. If you have little or no credit history it will not affect your application in a negative way. As far as we're concerned no credit equals good credit.</p>
      <p>REFERENCES: We will want to contact your current and perhaps your former landlord for references. The rental reference is an extremely important factor in evaluating prospective tenants so make sure your application includes accurate phone numbers for your current and former landlord. NO Evictions</p>
    </div>
    <div class="abs read-more">Read More</div>

    <p class="abs policy">Brighthold Property Management Inc. does not discriminate based on a person's race, color, religion, sex, sexual orientation, national origin, ancestry, source of income, age, disability, whether the person is married, or whether there are children under the age of 18 in the person's household.</p>

    <address class="abs contact" style="font-style:normal">
      Brighthold Property Management Inc.<br>
      4820 Lakeview Blvd. #310<br>
      Sacramento, CA. 95822<br>
      Cell (916) 555-0142 or Offc. (916) 555-0187<br>
      <u>tomhale@brighthold.biz</u>
    </address>

    <form>
      <div class="abs lbl" style="left:583px;top:3113px">First Name</div>
      <div class="abs lbl" style="left:816px;top:3113px">Last Name</div>
      <div class="abs field" style="left:583px;top:3135px">Type here</div>
      <div class="abs field" style="left:816px;top:3135px">Type here</div>
      <div class="abs lbl" style="left:583px;top:3176px">E-mail Address</div>
      <div class="abs lbl" style="left:816px;top:3176px">Phone Number</div>
      <div class="abs field" style="left:583px;top:3198px">Type here</div>
      <div class="abs field" style="left:816px;top:3198px">Type here</div>
      <div class="abs lbl" style="left:583px;top:3236px">Comments</div>
      <div class="abs field" style="left:583px;top:3257px;width:442px;height:77px;padding-top:28px">Type here</div>
      <div class="abs lbl" style="left:583px;top:3350px">Fax Number</div>
      <div class="abs lbl" style="left:816px;top:3350px">Prefered method of contact:</div>
      <div class="abs field" style="left:583px;top:3371px">Type here</div>
      <div class="abs field" style="left:816px;top:3371px">Choice</div>
      <div class="abs btn" style="left:790px">SUBMIT</div>
      <div class="abs btn" style="left:916px">RESET</div>
    </form>
  </section>

  <!-- Band 3 -->
  <svg class="abs" style="left:0;top:3492px" width="1200" height="78" aria-hidden="true">
    <path d="M0 0 H1200 V78 Q700 40 0 22 Z" fill="var(--band)"/>
  </svg>

  <!-- Mortgage -->
  <section>
    <h2 class="abs section-h mortgage-h">Mortgage Info</h2>
    <div class="abs red-h" style="left:84px;top:3608px">Mortgage Calculator</div>
    <div class="abs summary">
      <b>Loan Summary</b>
      <div><span>Loan amount</span><span>:$150,000.00</span></div>
      <div><span>Loan length</span><span>:30 years</span></div>
      <div><span>Annual interest</span><span>:3.70%</span></div>
      <div><span>Pay periodicity</span><span>:Monthly</span></div>
      <div><span>Monthly payment</span><span>:$690.42</span></div>
      <div><span>Total paid</span><span>:$248,552.81</span></div>
      <div><span>Total interest</span><span>:$98,552.81</span></div>
      <div><span>Total periods</span><span>:360</span></div>
    </div>
    <div class="abs params-h">Loan Parameters</div>
    <div class="abs small" style="left:388px;top:3690px">Loan amount:$</div>
    <div class="abs small" style="left:564px;top:3690px">Loan length:</div>
    <div class="abs mini" style="left:388px;top:3716px;width:88px">150000</div>
    <div class="abs mini" style="left:564px;top:3716px;width:52px;text-align:center">30</div>
    <div class="abs small" style="left:622px;top:3720px">Year</div>
    <div class="abs small" style="left:388px;top:3744px">Annual interest:</div>
    <div class="abs small" style="left:564px;top:3744px">Pay periodicity:</div>
    <div class="abs mini" style="left:388px;top:3767px;width:65px;text-align:center">3.7</div>
    <div class="abs small" style="left:462px;top:3771px">%</div>
    <div class="abs mini" style="left:564px;top:3767px;width:88px">Monthly</div>
    <div class="abs small" style="left:426px;top:3799px">Show amortization schedule</div>
    <div class="abs calc-btn">Calculate</div>

    <div class="abs red-h" style="left:767px;top:3614px">Mortgage Rates</div>
    <div class="abs rates">
      <div class="row"><span>National</span><span>Average Rate*</span></div>
      <div class="gap"></div>
      <div class="row"><span>30-Year FHA Rate</span><span>6.86%</span></div>
      <div class="row"><span>30-Year Fixed Rate</span><span>6.94%</span></div>
      <div class="row"><span>20-Year Fixed Rate</span><span>6.74%</span></div>
      <div class="row"><span>15-Year Fixed Rate</span><span>6.38%</span></div>
      <div class="note">* Conforming FNMA Loan Amount. Rates may include points.</div>
    </div>
  </section>

  <!-- Footer -->
  <footer>
    <div class="abs footer"></div>
    <div class="abs foot-brand"><i></i>BRIGHTHOLD</div>
    <svg class="abs" style="left:71px;top:4038px" width="210" height="32" aria-label="Social links" role="img">
      <g fill="none" stroke="#fff" stroke-width="2">
        <circle cx="16" cy="16" r="13"/>
        <circle cx="58" cy="16" r="13"/>
        <circle cx="100" cy="16" r="13"/>
        <circle cx="142" cy="16" r="13"/>
        <rect x="168" y="4" width="38" height="24" rx="2"/>
        <path d="M168 5 L187 19 L206 5"/>
      </g>
    </svg>
    <div class="abs foot-nav" style="left:355px;top:3930px">
      <div>Listing</div><div>Owners</div><div>Prospect Tenants</div>
    </div>
    <div class="abs foot-nav" style="left:643px;top:3930px">
      <div>About</div><div>Comunnity</div><div>Mortgage Info</div>
    </div>
    <div class="abs mascot" role="img" aria-label="Cartoon house mascot holding a key and waving"></div>
    <div class="abs legal">An Equal Opportunity Company. Equal Housing Opportunity. All rights reserved.<br>Copyright© 2024 BRIGHTHOLD PROPERTY MANAGEMENT INC</div>
  </footer>

</div>
</body>
</html>
```